Implant Denture Brochure

I would like to make a brochure to advertise implant dentures. This is for my dental clinic. I would like there to be some info about different implant denture options and advertise general cost. I like to use blue as a color and white. I may want to add or remove info based on the layout. Images of dentures with implants but no real photos just drawings or educational images. Real images of people smiling with dentures.

Upper
1. Implants for Upper Denture Implant Supported Removable $10,000 - $12,000 ( Includes fee for extraction of remaining upper teeth, in office sedation fees, Implant placement and necessary surgery of at least 4 implants, Does not include denture)
2. Upper Denture Implant Supported Fixed Bridge (Zirconia) $25,000 (Includes fee for extraction of all upper teeth, in office sedation fee, Implant placement and necessary surgery of at least 4 implants, includes temporary denture, and final denture)

Lower
1. Implants for Removable Lower Denture Implant Retained $5,000 - $7,000 (Includes fee for extraction of remaining lower teeth, in office sedation fees, Implant placement and necessary surgery of at least 2 implants, Does not include denture)

2. Implants for Removable Lower Denture Implant Supported $10,000 - $12,000 (Includes fee for extraction of remaining lower teeth, in office sedation fees, Implant placement and necessary surgery of at least 4 implants, Does not include denture)

3. Lower Denture Implant Supported Fixed Bridge (Zirconia) $25,000 (Includes fee for extraction of all upper teeth, in office sedation fee, Implant placement and necessary surgery of at least 4 implants, includes temporary denture, and final denture)

Copper Ridge Dental
#7 - 815 Lark Blvd N.
Copper Ridge, Alberta

```html
<!DOCTYPE html>
<html lang="en">
<head>
<meta charset="utf-8">
<title>Copper Ridge Dental – Implant Denture</title>
<link href="https://fonts.googleapis.com/css2?family=Source+Sans+3:wght@400;600;700&display=swap" rel="stylesheet">
<style>
:root{
  --page-bg:#5f6368;
  --white:#ffffff;
  --ink:#16181b;
  --navy:#1d4470;
  --deep:#24578d;
  --mid:#2f7cc0;
  --bright:#3a95d6;
  --sky:#7cc8ef;
  --accent:#37b3ea;
  --pill:#4a9ad7;
}
*{box-sizing:border-box;margin:0;padding:0}
html,body{width:1200px;height:1126px;overflow:hidden}
body{background:var(--page-bg);font-family:"Source Sans 3",Arial,sans-serif;position:relative}
.flyer{position:absolute;left:216px;top:20px;width:768px;height:1086px;background:var(--white);overflow:hidden}
.flyer-bg{position:absolute;inset:0;width:768px;height:1086px}
.hero-photo{position:absolute;left:0;top:0;width:768px;height:480px;
  background:linear-gradient(90deg,#f4f5f6 0%,#e3e6e8 35%,#d9c6a8 60%,#c9b58f 75%,#e6dcc8 100%)}
.brand{position:absolute;left:60px;top:170px;display:flex;align-items:center;gap:16px}
.brand-mark{width:46px;height:46px;border-radius:50%;background:var(--ink)}
.brand-name{font-weight:700;font-size:34px;line-height:1.05;color:var(--ink);letter-spacing:.5px;width:220px}
.title-pill{position:absolute;left:58px;top:282px;background:var(--pill);color:var(--white);
  font-weight:700;font-size:28px;letter-spacing:.5px;padding:8px 32px;border-radius:28px;
  box-shadow:0 4px 8px rgba(0,0,0,.15)}
.group{position:absolute;left:58px;width:672px;border:2px solid var(--sky);border-radius:24px;padding:30px 26px 16px 112px}
.group.upper{top:478px;height:196px}
.group.lower{top:712px;height:244px}
.group-tab{position:absolute;left:40px;top:-22px;width:250px;height:30px;border-radius:15px;
  background:linear-gradient(90deg,var(--sky),var(--accent));color:var(--white);font-weight:700;font-size:24px;
  line-height:30px;padding-left:90px}
.option{position:relative;font-size:13.5px;line-height:1.28;color:var(--white);margin-bottom:10px}
.option-icon{position:absolute;left:-92px;top:-6px;width:64px;height:64px;border-radius:50%;
  background:radial-gradient(circle,#ffffff 30%,#dcdfe2 100%);border:3px solid #eef1f3}
.option-name{color:var(--accent);font-weight:700}
.option-name::before{content:"";display:inline-block;width:11px;height:11px;border-radius:50%;
  background:var(--accent);margin-right:5px;vertical-align:-1px;
  clip-path:circle(50%)}
.price{font-weight:600}
.contact{position:absolute;right:40px;top:968px;color:var(--white);font-size:15px}
.contact-line{display:flex;align-items:center;gap:8px;margin-bottom:6px}
.contact-line.phone{font-size:18px}
.contact-icon{width:20px;height:20px;flex:none}
.website{position:absolute;left:40px;top:1040px;font-size:24px;color:var(--ink)}
.website strong{font-weight:700}
</style>
</head>
<body>
<main class="flyer">
  <div class="hero-photo" role="img" aria-label="Photo of a smiling senior couple embracing in a bright room"></div>
  <svg class="flyer-bg" viewBox="0 0 768 1086" aria-hidden="true">
    <defs>
      <linearGradient id="panelBlue" x1="0" y1="0" x2="0.4" y2="1">
        <stop offset="0" stop-color="#1d4470"/>
        <stop offset="0.55" stop-color="#2a6aa8"/>
        <stop offset="1" stop-color="#3a8fd2"/>
      </linearGradient>
      <linearGradient id="skyBand" x1="0" y1="0" x2="1" y2="0">
        <stop offset="0" stop-color="#9bd6f3"/>
        <stop offset="1" stop-color="#2aa3e0"/>
      </linearGradient>
    </defs>
    <path d="M420 0 L768 0 L768 250 C720 140 600 70 420 0Z" fill="#8fd0f1"/>
    <path d="M0 452 C240 490 560 470 768 330 L768 360 C560 500 240 520 0 488Z" fill="url(#skyBand)"/>
    <path d="M0 478 C240 512 560 492 768 352 L768 1086 L0 1086Z" fill="url(#panelBlue)"/>
    <path d="M0 1018 C150 975 330 975 470 1086 L0 1086Z" fill="#7cc8ef"/>
    <path d="M0 1028 C150 988 320 990 450 1086 L0 1086Z" fill="#ffffff"/>
  </svg>

  <div class="brand">
    <span class="brand-mark"></span>
    <span class="brand-name">Copper Ridge Dental</span>
  </div>
  <div class="title-pill">IMPLANT DENTURE</div>

  <section class="group upper">
    <h2 class="group-tab">UPPER</h2>
    <p class="option"><span class="option-icon" role="img" aria-label="Illustration of an upper denture on implants"></span>
      <span class="option-name">Implants for Upper Denture Implant Supported Removable</span> <span class="price">$10,000 - $12,000</span> (Includes fee for extraction of remaining upper teeth, in office sedation fees, Implant placement and necessary surgery of at least 4 implants, Does not include denture)</p>
    <p class="option" style="margin-top:16px"><span class="option-icon" role="img" aria-label="Illustration of an upper fixed bridge on implants"></span>
      <span class="option-name">Upper Denture Implant Supported Fixed Bridge (Zirconia)</span> <span class="price">$25,000</span> (Includes fee for extraction of all upper teeth, in office sedation fee, Implant placement and necessary surgery of at least 4 implants, includes temporary denture, and final denture)</p>
  </section>

  <section class="group lower">
    <h2 class="group-tab">LOWER</h2>
    <p class="option"><span class="option-icon" role="img" aria-label="Illustration of a lower denture retained by implants"></span>
      <span class="option-name">Implants for Removable Lower Denture Implant Retained</span> <span class="price">$5,000 - $7,000</span> (Includes fee for extraction of remaining lower teeth, in office sedation fees, Implant placement and necessary surgery of at least 2 implants, Does not include denture)</p>
    <p class="option"><span class="option-icon" role="img" aria-label="Illustration of a removable lower denture on implants"></span>
      <span class="option-name">Implants for Removable Lower Denture Implant Supported</span> <span class="price">$10,000 - $12,000</span> (Includes fee for extraction of remaining lower teeth, in office sedation fees, Implant placement and necessary surgery of at least 4 implants, Does not include denture)</p>
    <p class="option"><span class="option-icon" role="img" aria-label="Illustration of a lower fixed bridge on implants"></span>
      <span class="option-name">Lower Denture Implant Supported Fixed Bridge (Zirconia)</span> <span class="price">$25,000</span> (Includes fee for extraction of all upper teeth, in office sedation fee, Implant placement and necessary surgery of at least 4 implants, includes temporary denture, and final denture)</p>
  </section>

  <address class="contact" style="font-style:normal">
    <div class="contact-line phone">
      <svg class="contact-icon" viewBox="0 0 20 20" aria-hidden="true"><circle cx="10" cy="10" r="10" fill="#16181b"/><path d="M7 5.5l1.6 2.4-1 1c.6 1.3 1.5 2.2 2.8 2.8l1-1 2.4 1.6-.9 1.7c-3.6-.2-6.8-3.4-7-7z" fill="#fff"/></svg>
      +1 403-555-0187</div>
    <div class="contact-line">
      <svg class="contact-icon" viewBox="0 0 20 20" aria-hidden="true"><circle cx="10" cy="10" r="10" fill="#16181b"/><path d="M10 5l5 4.5h-1.5V14h-2.5v-3H9v3H6.5V9.5H5z" fill="#fff"/></svg>
      #7 - 815 Lark Blvd N. Copper Ridge, Alberta</div>
  </address>

  <p class="website">www.<strong>copperridgedental</strong>.ca</p>
</main>
</body>
</html>
```